New boutique hotel for tourists, with hint of art deco styling

This is a new, soon to be completed, boutique hotel in Sydney. A letterhead with a logo is required. Less emphasis on the word "boutique". Perhaps the word could be screened to be lighter in colour (or print intensity). Would like a simple, clear, easy-to read, sans serif type face. The information on the letterhead is:
Mrs Tolliver Boutique Hotel
412 Quenby Street,
Larchmere, NSW, 2047
Australia
Tel: +61 2 9468-0000
mrstolliverhotel@quelmail.example
mrstolliverhotel.example.au
ABN 47 902 365 184

Target Market(s)

travellers, tourists, various ages

Industry/Entity Type

Hospitality

Contact Information for Business Card

Mrs Tolliver Boutique Hotel
412 Quenby Street,
Larchmere, NSW, 2047
Telephone: (02) 9468-0000
www.mrstolliverhotel.example.au
mrstolliverhotel@quelmail.example
ABN 47 902 365 184

Logo Text

suggest playing with the letter "T"

Font styles to use
Sans Serif

Colors
3176b5

Requirements
Must have
• ABN to be very small.
• Must be clear, easy to read and in a sans serif typeface, please!
Nice to have
• The word "Boutique" should be less intense in appearance to the rest of the name, or even "Boutique Hotel" can have less prominence than "Mrs Tolliver".
Should not have
• No serif typeface. Sans serif only will be accepted.

```html
<!DOCTYPE html>
<html lang="en">
<head>
<meta charset="utf-8">
<title>Mrs Tolliver Boutique Hotel – Letterhead</title>
<link rel="stylesheet" href="https://fonts.googleapis.com/css2?family=Arimo:wght@700&family=Didact+Gothic&display=swap">
<style>
  :root {
    --paper: #ffffff;
    --ink-grey: #a6a6a8;
    --ink-soft: #8c8c8e;
    --blush: #fdeeee;
    --rose: #f2b6c0;
  }
  html, body {
    margin: 0;
    padding: 0;
    overflow: hidden;
    background: var(--paper);
  }
  .letterhead {
    position: relative;
    width: 848px;
    height: 1200px;
    background: var(--paper);
    overflow: hidden;
  }
  .brand {
    position: absolute;
    left: 46px;
    top: 70px;
    display: flex;
    align-items: center;
    gap: 16px;
  }
  .brand-dot {
    width: 30px;
    height: 30px;
    border-radius: 50%;
    background: var(--rose);
    flex: none;
  }
  .brand-name {
    font-family: "Arimo", Arial, sans-serif;
    font-weight: 700;
    color: var(--ink-grey);
    line-height: 1.05;
    letter-spacing: -1px;
  }
  .brand-name .line-main {
    display: block;
    font-size: 56px;
  }
  .brand-name .line-sub {
    display: block;
    font-size: 28px;
    letter-spacing: 0;
    margin-top: 6px;
  }
  .footer-band {
    position: absolute;
    left: 0;
    top: 998px;
    width: 848px;
    height: 202px;
    background: var(--blush);
  }
  .footer-name {
    position: absolute;
    left: 30px;
    top: 22px;
    margin: 0;
    font-family: "Arimo", Arial, sans-serif;
    font-weight: 700;
    font-size: 31px;
    letter-spacing: -0.5px;
    color: var(--ink-grey);
  }
  .contact {
    position: absolute;
    margin: 0;
    font-family: "Didact Gothic", "Century Gothic", sans-serif;
    font-size: 19px;
    line-height: 29px;
    color: var(--ink-soft);
    letter-spacing: -0.3px;
  }
  .contact-email { left: 31px; top: 76px; }
  .contact-abn { left: 35px; top: 136px; }
  .contact-address { left: 345px; top: 80px; }
  .contact-web { right: 30px; top: 76px; text-align: right; }
  .contact-phone { right: 30px; top: 136px; text-align: right; }
</style>
</head>
<body>
  <main class="letterhead">
    <header class="brand">
      <span class="brand-dot" aria-hidden="true"></span>
      <div class="brand-name">
        <span class="line-main">Mrs Tolliver</span>
        <span class="line-sub">Boutique Hotel</span>
      </div>
    </header>

    <footer class="footer-band">
      <p class="footer-name">Mrs Tolliver</p>
      <p class="contact contact-email">mrstolliverhotel@quelmail.example</p>
      <p class="contact contact-abn">ABN 47 902 365 184</p>
      <p class="contact contact-address">412 Quenby Street<br>Larchmere, NSW, 2047<br>Australia</p>
      <p class="contact contact-web">mrstolliverhotel.example.au</p>
      <p class="contact contact-phone">Tel: +61 2 9468-0000</p>
    </footer>
  </main>
</body>
</html>
```